established boer goat stud and dorper sheep stud need an updated look

I need a design to promote the boer goat stud and dorper sheep stud, so its clear and simple
Updates

Details for business card design Wirrabel Boers and Dorper Sheep Stud. I would like silhouette animal head or full body of a boer goat (not a dairy breed goat) and Dorper sheep. Contact: Maree Dalton +61 412578304 Sandra Pollock +61 438615027 Mooroopna North Victoria Australia Email: wirrabel5184@mailvane.com

Industry/Entity Type

Agriculture

Contact Information for Business Card

Wirrabel Boers and Dorper Sheep Stud Maree Dalton +61 412578304 Sandra Pollock +61 438615027 wirrabel5184@mailvane.com Tallowbark Victoria Australia

Colors
EE7325
F08F49
F5BC92
FAE3D3
FDF4ED

Requirements
Must have
• My Boer Goats and Dorper Sheep images see my photos

```html
<!DOCTYPE html>
<html lang="en">
<head>
<meta charset="utf-8">
<title>Wirrabel Boers &amp; Dorper Sheep Stud – Business Card</title>
<link rel="stylesheet" href="https://fonts.googleapis.com/css2?family=Oswald:wght@500;600;700&family=Arimo:wght@400&display=swap">
<style>
  :root {
    --backdrop: #2a2a2a;
    --card-white: #ffffff;
    --ink: #111111;
    --ink-soft: #1c1c1c;
    --photo-grass: #4f7a3a;
    --photo-soil: #5a4838;
    --photo-coat: #e9e6e1;
    --photo-tan: #9a5a34;
    --veil: rgba(20, 20, 20, 0.42);
    --title-light: #ffffff;
  }
  * { box-sizing: border-box; margin: 0; padding: 0; }
  html, body {
    width: 1200px;
    height: 930px;
    overflow: hidden;
    background: var(--backdrop);
  }
  .canvas {
    position: relative;
    width: 1200px;
    height: 930px;
  }
  .card {
    position: absolute;
    left: 240px;
    width: 720px;
    height: 411px;
    border-radius: 16px;
    overflow: hidden;
    box-shadow: 0 10px 28px rgba(0,0,0,0.45);
  }
  .card--front { top: 34px; }
  .card--back  { top: 485px; background: var(--card-white); }

  /* front */
  .front-photo {
    position: absolute;
    inset: 0;
    background:
      linear-gradient(160deg, var(--photo-soil) 0%, #6b5644 30%, transparent 31%),
      radial-gradient(ellipse 45% 40% at 50% 62%, var(--photo-coat) 0%, #d8d2ca 55%, transparent 75%),
      radial-gradient(ellipse 25% 22% at 72% 35%, var(--photo-tan) 0%, transparent 80%),
      linear-gradient(100deg, var(--photo-grass) 0%, #3f6230 22%, var(--photo-soil) 45%, #4b3d30 100%);
  }
  .front-veil {
    position: absolute;
    inset: 0;
    background: var(--veil);
  }
  .front-title {
    position: absolute;
    left: 0;
    right: 0;
    top: 186px;
    text-align: center;
    font-family: 'Oswald', sans-serif;
    font-weight: 600;
    font-size: 36px;
    letter-spacing: 2px;
    color: var(--title-light);
    text-transform: uppercase;
  }

  /* back */
  .back-art {
    position: absolute;
    inset: 0;
  }
  .back-brand {
    position: absolute;
    left: 46px;
    top: 204px;
    font-family: 'Oswald', sans-serif;
    color: var(--ink);
    text-transform: uppercase;
    line-height: 1;
  }
  .back-brand__main {
    display: block;
    font-weight: 700;
    font-size: 32px;
    letter-spacing: 1px;
  }
  .back-brand__sub {
    display: block;
    font-weight: 600;
    font-size: 18px;
    letter-spacing: 1px;
    margin-top: 2px;
  }
  .contact-list {
    position: absolute;
    left: 46px;
    top: 272px;
    list-style: none;
    font-family: 'Arimo', sans-serif;
    font-size: 18px;
    line-height: 27px;
    color: var(--ink-soft);
  }
</style>
</head>
<body>
<main class="canvas">

  <section class="card card--front" aria-label="Card front">
    <div class="front-photo" role="img" aria-label="Photo of Boer goats standing in a paddock"></div>
    <div class="front-veil"></div>
    <h1 class="front-title">Wirrabel Boers &amp; Dorper Sheep Stud</h1>
  </section>

  <section class="card card--back" aria-label="Card back">
    <svg class="back-art" width="720" height="411" viewBox="0 0 720 411">
      <defs>
        <linearGradient id="herdTones" x1="0" y1="0" x2="1" y2="1">
          <stop offset="0" stop-color="#4f7a3a"/>
          <stop offset="0.3" stop-color="#6b5a48"/>
          <stop offset="0.55" stop-color="#ece9e4"/>
          <stop offset="0.8" stop-color="#a4643c"/>
          <stop offset="1" stop-color="#e6e2dc"/>
        </linearGradient>
        <linearGradient id="swooshFade" x1="0" y1="0" x2="1" y2="0">
          <stop offset="0" stop-color="#000" stop-opacity="0.9"/>
          <stop offset="0.6" stop-color="#000" stop-opacity="1"/>
          <stop offset="1" stop-color="#000" stop-opacity="0.3"/>
        </linearGradient>
      </defs>
      <path class="swoosh-line" d="M236 0 C226 190 366 304 720 318" fill="none" stroke="url(#swooshFade)" stroke-width="7"/>
      <path class="herd-photo" role="img" aria-label="Photo of Boer goats resting by a tree"
            d="M250 0 C240 180 376 290 720 304 L720 0 Z" fill="url(#herdTones)"/>
    </svg>

    <h2 class="back-brand">
      <span class="back-brand__main">Wirrabel Boers</span>
      <span class="back-brand__sub">&amp; Dorper Sheep Stud</span>
    </h2>

    <ul class="contact-list">
      <li>MAREE DALTON +61 412578304</li>
      <li>SANDRA POLLOCK +61 438615027</li>
      <li>Email : wirrabel5184@mailvane.com</li>
      <li>Address : Tallowbark Victoria Australia</li>
    </ul>
  </section>

</main>
</body>
</html>
```